Contemporary Business card for Event Manager

Needed for my startup events company in Melbourne. Events I manage will be based within the fashion industry, sporting events, product launches etc. Not weddings or small dinner parties. Therfore I am after something professional and aimed at high end corporate market; but with the added emphasis on not being too conservative or boring. I am happy with a pop of colour e.g. yellow or copper foil.

Target Market(s)

fashion industry, design industry, high end sporting events e.g. Polo, Grand Prix, corporate clients,

Industry/Entity Type

Fashion

Contact Information for Business Card

side 1
Lucy Brandt (can be upper or lower case, have a feature full stop between first and surname, or at the end of the nameetc) I am open to ideas. I would also be fine with my initials or name as a logo on the front (if this is the case my full name would need to go on the second side of the card.
2nd side:
Mobile: +61 400 817 263
email: lucy.brandt@mailnest.com.au

on one side of the card:
event management | brand activation | Advisory Services

Font styles to use
Serif
Sans Serif

Requirements
Must have
• side 2 must have
• mobile number
• email address
• event management | brand activation | Advisory Services
• ** my full name (Lucy Brandt) must be on the card somewhere)
Nice to have
• 1st side
• I see the card stock being either a dark grey, light grey, natural white or black (all matt colours on unprocessed card). I see the writing being copper foil, or foil white or foil black.
• To give you a feel for me, think: contemporary, minimalist, I love line drawings, concrete, white with grey vein marble, copper, white, grey, black...yes I do like colour....yellow (but pops of colour) ;) I would like the card to look designer but 'on trend' as I deal with a lot of design and fashion clients....styles - think the sophistication and simplicity of Vireaux or urban contemporary.
• some examples of what I like. Although please don't leet this limit you...I really am happy to have something a little more urban or design focused like a line drawing of an object, person too or a photo image too.
• https://www.moodtackle.com/pin/830165427719302846/
• https://www.moodtackle.com/pin/607281935540173268/
• https://www.moodtackle.com/pin/318746205913457092/
• https://www.moodtackle.com/pin/41983627530918476/
• https://www.moodtackle.com/pin/53128940672419087/
• https://www.moodtackle.com/pin/90316284750638152/
• https://www.moodtackle.com/pin/734092618450362918/
• https://www.moodtackle.com/pin/926354081736215407/
• https://www.moodtackle.com/pin/481627093518704356/
Should not have
• should not look commercial or have cartoonish looking logos. However happy with a simple line drawing or logo with initials etc.

```html
<!DOCTYPE html>
<html lang="en">
<head>
<meta charset="utf-8">
<title>Lucy Brandt — Business Card</title>
<link rel="stylesheet" href="https://fonts.googleapis.com/css2?family=Tinos&display=swap">
<style>
  :root {
    --backdrop: #e4e2df;
    --card-black: #0d0d0d;
    --card-edge: #1c1c1c;
    --copper-light: #f2b9a0;
    --copper-mid: #c97a5c;
    --copper-dark: #8e4a33;
    --shadow: rgba(0, 0, 0, 0.28);
  }
  * { box-sizing: border-box; margin: 0; padding: 0; }
  html, body {
    width: 1200px;
    height: 892px;
    overflow: hidden;
    background: var(--backdrop);
    font-family: "Tinos", "Times New Roman", serif;
  }
  .canvas {
    width: 1200px;
    height: 892px;
    display: flex;
    align-items: center;
    justify-content: center;
    gap: 48px;
  }
  .card {
    width: 520px;
    height: 318px;
    border-radius: 22px;
    background: linear-gradient(160deg, var(--card-edge) 0%, var(--card-black) 45%, var(--card-black) 100%);
    box-shadow: 0 18px 40px var(--shadow);
    position: relative;
    color: var(--copper-mid);
  }
  .foil {
    background: linear-gradient(100deg, var(--copper-dark) 0%, var(--copper-light) 30%, var(--copper-mid) 55%, var(--copper-light) 78%, var(--copper-dark) 100%);
    -webkit-background-clip: text;
    background-clip: text;
    color: transparent;
  }
  .card-front {
    display: flex;
    align-items: center;
    justify-content: center;
  }
  .card-front .name {
    font-size: 58px;
    letter-spacing: 1px;
    line-height: 1;
    padding-bottom: 6px;
  }
  .card-back {
    display: flex;
    align-items: center;
    justify-content: center;
  }
  .contact {
    text-align: left;
    line-height: 1.25;
  }
  .contact .phone {
    font-size: 27px;
    letter-spacing: 1px;
    margin-bottom: 6px;
    display: inline-block;
  }
  .contact .email {
    font-size: 16px;
    display: block;
    margin-bottom: 14px;
  }
  .services {
    list-style: none;
    padding-left: 62px;
    font-size: 18px;
    line-height: 1.15;
  }
</style>
</head>
<body>
  <main class="canvas">
    <section class="card card-front" aria-label="Card front">
      <h1 class="name foil">Lucy.Brandt</h1>
    </section>
    <section class="card card-back" aria-label="Card back">
      <div class="contact">
        <span class="phone foil">61 400 817 263</span>
        <span class="email foil">lucy.brandt@mailnest.com.au</span>
        <ul class="services">
          <li class="foil">event management</li>
          <li class="foil">brand activation</li>
          <li class="foil">Advisory Services</li>
        </ul>
      </div>
    </section>
  </main>
</body>
</html>
```